Geschäftspapiere für Jobwebseite
Zielgruppe
Hier finden sie alle Informationen zu unserem Unternehmen:
https://www.sauberwerk-stelle.com
Aufgabenstellung
Gerne von den Farben angelehnt an die Website ein modernes Briefpapier gestalten.

```html
<!DOCTYPE html>
<html lang="de">
<head>
<meta charset="utf-8">
<title>Briefpapier Sauberwerk-Stelle</title>
<link href="https://fonts.googleapis.com/css2?family=Poppins:wght@400;500;700&display=swap" rel="stylesheet">
<style>
  :root {
    --backdrop: #e6e6e8;
    --paper: #ffffff;
    --green: #1f9b3c;
    --green-dark: #168a33;
    --slate: #3c3c48;
    --ink: #222226;
  }
  * { margin: 0; padding: 0; box-sizing: border-box; }
  html, body { width: 1053px; height: 1200px; overflow: hidden; }
  body {
    background: var(--backdrop);
    font-family: "Poppins", sans-serif;
    color: var(--ink);
    position: relative;
  }
  .letterhead {
    position: absolute;
    left: 109px; top: 56px;
    width: 832px; height: 1079px;
    background:
      radial-gradient(ellipse 90% 70% at 100% 0%, rgba(60,180,100,0.5) 0%, rgba(120,210,150,0.22) 40%, rgba(255,255,255,0) 72%),
      radial-gradient(ellipse 65% 42% at 0% 100%, rgba(80,80,95,0.35) 0%, rgba(160,160,170,0.15) 50%, rgba(255,255,255,0) 82%),
      var(--paper);
    overflow: hidden;
  }
  .accent-top {
    position: absolute; right: 0; top: 0;
    width: 200px; height: 340px;
    background: linear-gradient(215deg, var(--green-dark) 0%, rgba(40,160,70,0.85) 30%, rgba(90,195,125,0.4) 60%, rgba(255,255,255,0) 85%);
  }
  .accent-bottom {
    position: absolute; left: 0; bottom: 0;
    width: 200px; height: 340px;
    background: linear-gradient(35deg, var(--slate) 0%, rgba(70,70,85,0.7) 30%, rgba(150,150,160,0.3) 60%, rgba(255,255,255,0) 85%);
  }
  .brand {
    position: absolute; left: 18px; top: 126px;
    font-weight: 700; font-size: 13px; letter-spacing: 0.1px;
    color: var(--ink);
  }
  .sender {
    position: absolute; left: 15px; top: 162px;
    font-size: 9.5px; color: var(--ink);
  }
  .contact {
    position: absolute; left: 549px; top: 92px;
    list-style: none;
  }
  .contact li {
    display: flex; align-items: center;
    height: 22.5px; font-size: 9.5px; font-weight: 500;
  }
  .contact svg { width: 19px; height: 19px; margin-right: 8px; flex: none; }
  .footer {
    position: absolute; top: 1029px; left: 254px;
    display: flex; font-size: 8.5px; line-height: 16px; font-weight: 500;
  }
  .footer .col { padding: 2px 12px; }
  .footer .col:first-child { padding-left: 0; }
  .footer .col + .col { border-left: 1.5px solid var(--ink); }
</style>
</head>
<body>
  <div class="letterhead">
    <div class="accent-top" role="img" aria-label="Grüne Farbfläche als Eckakzent oben rechts"></div>
    <div class="accent-bottom" role="img" aria-label="Graue Farbfläche als Eckakzent unten links"></div>

    <div class="brand">SAUBERWERK-STELLE.de</div>
    <p class="sender">Lena Vorholt / Birkenweg 12 / D-40210 Nordtal</p>

    <ul class="contact">
      <li>
        <svg viewBox="0 0 20 20"><circle cx="10" cy="10" r="10" fill="var(--green)"/><path d="M7 5.5l1.6-.3 1 2.2-1 .8a6 6 0 0 0 2.4 2.4l.8-1 2.2 1-.3 1.6c-3.8.3-7-2.9-6.7-6.7z" fill="#fff"/></svg>
        0211.4405817
      </li>
      <li>
        <svg viewBox="0 0 20 20"><circle cx="10" cy="10" r="10" fill="var(--green)"/><rect x="7" y="5" width="6" height="3" fill="#fff"/><rect x="5" y="8" width="10" height="5" rx="1" fill="#fff"/><rect x="7" y="11" width="6" height="4" fill="#fff" stroke="var(--green)" stroke-width="0.8"/></svg>
        0172.3304918
      </li>
      <li>
        <svg viewBox="0 0 20 20"><circle cx="10" cy="10" r="10" fill="var(--green)"/><path d="M5 9.8l9.5-4-2 9-2.6-2.3-1.5 1.5v-2.6l4-3.6-5 3z" fill="#fff"/></svg>
        info@sauberwerk-stelle.de
      </li>
      <li>
        <svg viewBox="0 0 20 20"><circle cx="10" cy="10" r="10" fill="var(--green)"/><circle cx="10" cy="10" r="6" fill="#fff"/><circle cx="10" cy="10" r="2" fill="var(--green)"/></svg>
        sauberwerk-stelle.de
      </li>
    </ul>

    <div class="footer">
      <div class="col">Steuer-Nr.<br>DE204517380</div>
      <div class="col">Bankverbindung:<br>Stadtsparkasse Nordtal</div>
      <div class="col">BIC NORDDE33XXX<br>IBAN DE12 3004 0500 0007 3321 45</div>
    </div>
  </div>
</body>
</html>
```